Alaska Law Firm Needs a Sticker Design

We need a design for stickers to put on already-printed brochures. We mail the brochures to potential clients so they can learn more about accident-induced injuries, insurance claims, legal representation, and our own law firm.

One of our lawyers wrote a book that provides a helpful overview of personal injury claims. We are offering this book for free to anyone who calls and requests it. Therefore, the sticker design should include one of the following phrases, or something very similar:
a) "Still have questions? Call and request our book-- for free!"
b) "Still have questions about auto accident claims? Call and request our book today."
c) "Still have questions about filing a claim? Call and request a free copy of our book."
d) "Still have questions? Call us today to request a free copy of our book, Clear Lanes Ahead."
e) "To learn more about automobile accidents and insurance, call today and request a free copy of our book."

The sticker should be approximately 3"x3" and may be a circle, square, rectangle, or ellipsis. The sticker will be placed on the back of the folder, which is light blue. We would like the sticker to match the color scheme of our website and the folder.

I will upload an image of the book cover as soon as I obtain it.

Law Firm

Font styles to use
Serif
Sans Serif

Requirements
Should not have
• Bright colors that aren't already used in the folder design. e.g. no bright orange, pink, chartreuse, turquoise, yellow, red.

```html
<!DOCTYPE html>
<html lang="en">
<head>
<meta charset="UTF-8">
<title>Clear Lanes Ahead – Free Book Sticker</title>
<link href="https://fonts.googleapis.com/css2?family=Bebas+Neue&family=Open+Sans:wght@400;600;800&family=Montserrat:wght@500&display=swap" rel="stylesheet">
<style>
  :root {
    --page-bg: #ececec;
    --sticker-border: #ffffff;
    --sky: #d7e5f6;
    --navy: #133d66;
    --ink: #111a3f;
    --cover-band: #16184a;
    --white: #ffffff;
    --photo-sky: #c9d8e4;
    --photo-green: #6fa24a;
  }
  * { margin: 0; padding: 0; box-sizing: border-box; }
  html, body { width: 1200px; height: 1085px; overflow: hidden; }
  body { background: var(--page-bg); position: relative; font-family: "Open Sans", sans-serif; }

  .sticker {
    position: absolute; left: 77px; top: 20px;
    width: 1045px; height: 1045px;
    background: var(--sticker-border);
    padding: 19px;
  }
  .sticker-face {
    position: relative; width: 100%; height: 100%;
    background: var(--sky); overflow: hidden;
  }
  .headline {
    position: absolute; top: 21px; left: 0; width: 100%;
    text-align: center; font-family: "Bebas Neue", sans-serif;
    color: var(--navy); font-size: 158px; line-height: 1; letter-spacing: 1px;
  }
  .headline-sub {
    position: absolute; top: 168px; left: 0; width: 100%;
    text-align: center; font-family: "Bebas Neue", sans-serif;
    font-size: 88px; line-height: 1; letter-spacing: 24px; padding-left: 24px;
    color: var(--white); -webkit-text-stroke: 3px var(--navy);
  }

  .book {
    position: absolute; background: var(--white);
    display: flex; flex-direction: column; align-items: center;
    box-shadow: 0 0 6px rgba(0,0,0,0.12);
  }
  .book--side { top: 337px; width: 201px; height: 316px; filter: blur(4px); opacity: 0.85; }
  .book--left { left: 274px; }
  .book--right { left: 524px; }
  .book--front { left: 368px; top: 275px; width: 282px; height: 438px; padding: 6px; }

  .book-author { margin-top: 14px; font-size: 17px; color: var(--ink); letter-spacing: 0.5px; }
  .book-title {
    margin-top: 8px; text-align: center; font-weight: 800;
    font-size: 33px; line-height: 1.02; color: var(--ink); letter-spacing: -0.5px;
  }
  .book-photo {
    margin-top: 8px; width: 100%; flex: 1;
    background: linear-gradient(180deg, var(--photo-sky) 0%, #b8cfa0 45%, var(--photo-green) 100%);
  }
  .book-tagline {
    width: 100%; background: var(--cover-band); color: var(--white);
    text-align: center; font-size: 13px; line-height: 1.25; padding: 6px 4px 7px;
    text-transform: uppercase;
  }
  .book--side .book-title { font-size: 24px; }
  .book--side .book-author { font-size: 12px; margin-top: 10px; }
  .book--side .book-tagline { font-size: 9px; }

  .offer-band {
    position: absolute; left: 0; top: 717px; width: 100%; height: 216px;
    background: var(--navy); color: var(--white);
    font-family: "Bebas Neue", sans-serif; text-align: center;
  }
  .offer-lead { position: absolute; top: 18px; width: 100%; font-size: 54px; line-height: 1; letter-spacing: 1px; }
  .offer-main { position: absolute; top: 86px; width: 100%; font-size: 128px; line-height: 1; letter-spacing: 2px; }

  .phone {
    position: absolute; left: 0; top: 946px; width: 100%;
    text-align: center; font-family: "Montserrat", sans-serif; font-weight: 500;
    font-size: 40px; line-height: 52px; color: #111; letter-spacing: 0.5px;
  }
</style>
</head>
<body>
  <div class="sticker">
    <div class="sticker-face">
      <div class="headline">Still Have</div>
      <div class="headline-sub">Questions?</div>

      <div class="book book--side book--left" aria-hidden="true">
        <div class="book-author">DANIEL R. HOLLIS</div>
        <div class="book-title">CLEAR LANES<br>AHEAD</div>
        <div class="book-photo"></div>
        <div class="book-tagline">A simple guide to your<br>car crash injury claim</div>
      </div>
      <div class="book book--side book--right" aria-hidden="true">
        <div class="book-author">DANIEL R. HOLLIS</div>
        <div class="book-title">CLEAR LANES<br>AHEAD</div>
        <div class="book-photo"></div>
        <div class="book-tagline">A simple guide to your<br>car crash injury claim</div>
      </div>

      <div class="book book--front">
        <div class="book-author">DANIEL R. HOLLIS</div>
        <div class="book-title">CLEAR LANES<br>AHEAD</div>
        <div class="book-photo" role="img" aria-label="Photo of a smiling family lying on the grass in a park beside a small red car"></div>
        <div class="book-tagline">A simple guide to your<br>car crash injury claim</div>
      </div>

      <div class="offer-band">
        <div class="offer-lead">Call &amp; Request Our Book</div>
        <div class="offer-main">For Free !!</div>
      </div>

      <div class="phone">(907 555-0142)</div>
    </div>
  </div>
</body>
</html>
```